Presentation Folder, for Cancer Awareness, VERY COLORFULL AND MODERN

This will be a standard size folder that will hold standard 8 1/2 x 11 papers with a business card slot on the flap, this is a very easy project with very little text and the design for the back page is already done so all you really have to do is make a very nice colorful front cover, you will see my attachments are labeled and I gave you alot of instructions, this should be a very fast easy project
Updates

Reason: there has not been enough quality designs, sorry

Target Market(s)

Our Target Market is Dr's that Deal with Cancer patients

Industry/Entity Type

Healthcare

Font styles to use
Serif

Colors

Designer to choose colors to be used in the design.

Requirements
Must have
• Project must be tasteful and look professional with the ribbons as the main focal point in the center of folder the folder should be a nice gray color to accent the color of the ribbons , the back page needs no design it is the" Sorvane Test" in the attachments I sent
Nice to have
• I would like the ribbons displayed in a row, I included a logo sample layout
• a picture on the front of the folder under the words Hereditary Cancer Screening - Then under that put the words - The Power of Knowledge - then add the picture I labeled Great Picture in the attachments

```html
<!DOCTYPE html>
<html lang="en">
<head>
<meta charset="utf-8">
<title>Hereditary Cancer Screening Folder</title>
<link href="https://fonts.googleapis.com/css2?family=Open+Sans:ital,wght@0,300;0,400;0,600;0,700;1,700&display=swap" rel="stylesheet">
<style>
  :root {
    --stage: #e3e3e3;
    --sheet: #ffffff;
    --rule: #555555;
    --brand-red: #c8413f;
    --ink: #3a3a3a;
    --muted: #8a8a8a;
    --violet: #b97ab6;
    --violet-deep: #9b5fa0;
    --sky: #2fa7de;
    --row-alt: #ededed;
    --lynch: #f6c443;
    --peutz: #c3c93c;
    --lifraumeni: #3fa84b;
    --cowden: #2aa6de;
    --gastric: #5f5f5f;
    --label: #2f9a48;
  }
  * { box-sizing: border-box; margin: 0; padding: 0; }
  html, body { width: 1200px; height: 778px; overflow: hidden; }
  body { background: var(--stage); font-family: "Open Sans", Arial, sans-serif; position: relative; }

  .panel { position: absolute; top: 30px; height: 718px; background: var(--sheet); border: 1px solid var(--rule); }
  .panel--back { left: 38px; width: 563px; }
  .panel--front { left: 600px; width: 564px; overflow: hidden; }

  .panel-label { position: absolute; top: 751px; font-size: 19px; color: var(--label); transform: translateX(-50%); }
  .panel-label--back { left: 306px; }
  .panel-label--front { left: 878px; }

  /* back */
  .brand-name { font-weight: 300; letter-spacing: 5px; color: var(--brand-red); }
  .back-brand { position: absolute; left: 52px; top: 52px; font-size: 15px; }
  .back-address { position: absolute; left: 52px; top: 78px; font-size: 5.6px; color: var(--muted); letter-spacing: .4px; line-height: 9px; }
  .menu-title { position: absolute; left: 330px; top: 51px; font-size: 17px; font-weight: 700; font-style: italic; color: var(--sky); }
  .menu-title span { font-weight: 700; }
  .clia { position: absolute; left: 365px; top: 86px; font-size: 5.6px; color: var(--muted); letter-spacing: .4px; }
  .clia b { color: #666; }

  .gene-table { position: absolute; left: 132px; top: 118px; width: 277px; }
  .gene-row { display: flex; height: 13.85px; align-items: center; font-size: 6.6px; }
  .gene-row:nth-child(even) { background: var(--row-alt); }
  .gene { width: 87px; padding-left: 5px; color: var(--violet); font-weight: 600; }
  .organs { color: var(--ink); font-weight: 600; }
  .gene-row--indent .gene { padding-left: 12px; }
  .section-head { height: 13.85px; display: flex; align-items: center; padding-left: 12px; font-size: 7.6px; color: #fff; letter-spacing: .3px; }
  .section-head--main { background: var(--violet); padding-left: 92px; }
  .section-head--lynch { background: var(--lynch); }
  .section-head--peutz { background: var(--peutz); }
  .section-head--lifraumeni { background: var(--lifraumeni); }
  .section-head--cowden { background: var(--cowden); }
  .section-head--gastric { background: var(--gastric); }

  /* front */
  .family-photo { position: absolute; left: 0; top: 150px; width: 564px; height: 360px;
    background: radial-gradient(ellipse at 50% 45%, rgba(214,196,176,.75) 0%, rgba(226,214,204,.55) 45%, rgba(255,255,255,0) 75%); }
  .awareness-ribbon { position: absolute; left: 150px; top: 130px; width: 220px; height: 360px; }
  .front-brand { position: absolute; left: 0; width: 100%; top: 78px; text-align: center; font-size: 11px; }
  .brand-dot { position: absolute; left: 270px; top: 44px; width: 25px; height: 25px; border-radius: 50%; background: var(--brand-red); }
  .cover-title { position: absolute; left: 0; width: 100%; top: 500px; text-align: center; font-weight: 300; font-size: 37px; line-height: 41px; color: var(--violet); }
  .cover-tagline { position: absolute; left: 0; width: 100%; top: 587px; text-align: center; font-weight: 300; font-size: 21px; color: var(--sky); }
  .cancer-list { position: absolute; left: 0; width: 100%; top: 642px; text-align: center; font-weight: 300; font-size: 16px; line-height: 27px; color: #555; }
</style>
</head>
<body>

<section class="panel panel--back">
  <div class="brand-name back-brand">HELIXORA</div>
  <div class="back-address">2870 MERIDIAN PARK WAY | SUITE B | ATLANTA, GA 30309<br>(tel) 555.210.4481 &nbsp;| (fax) 555.210.4482 &nbsp;| cs@helixora.com</div>
  <h1 class="menu-title">SORVANE <span>Test Menu</span></h1>
  <div class="clia">CLIA# 99Z4471205 | <b>HELIXORA.COM</b></div>

  <div class="gene-table">
    <div class="section-head section-head--main">CANCER-ASSOCIATED ORGAN/SYSTEMS</div>
    <div class="gene-group">
      <div class="gene-row"><span class="gene">APC</span><span class="organs">Colon</span></div>
      <div class="gene-row"><span class="gene">ATM</span><span class="organs">Breast/Pancreatic/Brain</span></div>
      <div class="gene-row"><span class="gene">BARD1</span><span class="organs">Breast/Ovarian</span></div>
      <div class="gene-row"><span class="gene">BMPR1A</span><span class="organs">Colon</span></div>
      <div class="gene-row"><span class="gene">BRCA1</span><span class="organs">Breast/Ovarian/Prostate</span></div>
      <div class="gene-row"><span class="gene">BRCA2</span><span class="organs">Breast/Ovarian/Prostate</span></div>
      <div class="gene-row"><span class="gene">BRIP1</span><span class="organs">Breast/Ovarian</span></div>
      <div class="gene-row"><span class="gene">CDK4</span><span class="organs">Melanoma</span></div>
      <div class="gene-row"><span class="gene">P16 (CDKN2A)</span><span class="organs">Melanoma/Breast/Pancreatic/Squamous</span></div>
      <div class="gene-row"><span class="gene">FANCC</span><span class="organs">Blood</span></div>
      <div class="gene-row"><span class="gene">MEN1</span><span class="organs">Thyroid/Parathyroid</span></div>
      <div class="gene-row"><span class="gene">MET</span><span class="organs">Renal/Hepatic</span></div>
      <div class="gene-row"><span class="gene">MRE11A</span><span class="organs">Ovarian/Breast</span></div>
      <div class="gene-row"><span class="gene">NBN</span><span class="organs">Breast/Ovarian/Prostate/Melanoma</span></div>
      <div class="gene-row"><span class="gene">NF1</span><span class="organs">Blood</span></div>
      <div class="gene-row"><span class="gene">NTRK1</span><span class="organs">Thyroid/Parathyroid</span></div>
      <div class="gene-row"><span class="gene">PALB2</span><span class="organs">Breast/Ovarian/Pancreatic</span></div>
      <div class="gene-row"><span class="gene">PTCH1</span><span class="organs">Melanoma/Brain/Breast/Colon</span></div>
      <div class="gene-row"><span class="gene">RAD50</span><span class="organs">Breast/Ovarian</span></div>
      <div class="gene-row"><span class="gene">RAD51C</span><span class="organs">Ovarian/Breast</span></div>
      <div class="gene-row"><span class="gene">RAD51D</span><span class="organs">Ovarian/Breast</span></div>
      <div class="gene-row"><span class="gene">RET</span><span class="organs">Lung/Thyroid/Parathyroid</span></div>
      <div class="gene-row"><span class="gene">SMAD4</span><span class="organs">Colon/Pancreas</span></div>
    </div>
    <div class="section-head section-head--lynch">LYNCH SYNDROME GENES</div>
    <div class="gene-group">
      <div class="gene-row gene-row--indent"><span class="gene">MLH1</span><span class="organs">Colorectal/Ovarian</span></div>
      <div class="gene-row gene-row--indent"><span class="gene">MSH2</span><span class="organs">Colorectal/Ovarian</span></div>
      <div class="gene-row gene-row--indent"><span class="gene">MSH6</span><span class="organs">Colorectal/Ovarian</span></div>
      <div class="gene-row gene-row--indent"><span class="gene">PMS2</span><span class="organs">Colorectal/Ovarian</span></div>
      <div class="gene-row gene-row--indent"><span class="gene">EPCAM</span><span class="organs">Colorectal</span></div>
    </div>
    <div class="section-head section-head--peutz">PEUTZ-JEGHERS SYNDROME GENE</div>
    <div class="gene-row gene-row--indent"><span class="gene">STK11</span><span class="organs">Breast/Ovarian/Melanoma/Colorectal/Lung</span></div>
    <div class="section-head section-head--lifraumeni">LI-FRAUMENI SYNDROME GENE</div>
    <div class="gene-group">
      <div class="gene-row gene-row--indent" style="background:#fff"><span class="gene">CHEK2</span><span class="organs">Breast/Ovarian/Prostate</span></div>
      <div class="gene-row gene-row--indent"><span class="gene">PT53</span><span class="organs">Breast/Bladder/Ovarian/Squamous</span></div>
    </div>
    <div class="section-head section-head--cowden">COWDEN SYNDROME GENE</div>
    <div class="gene-row gene-row--indent"><span class="gene">PTEN</span><span class="organs">Endometrium/Breast/Prostate/Lung</span></div>
    <div class="section-head section-head--gastric">HEREDITARY DIFFUSE GASTRIC CANCER SYNDROME GENE</div>
    <div class="gene-group">
      <div class="gene-row gene-row--indent" style="background:#fff"><span class="gene">CDH1</span><span class="organs">Breast/Gastric/Ovarian/Prostate</span></div>
      <div class="gene-row gene-row--indent"><span class="gene">VHL</span><span class="organs">Renal</span></div>
    </div>
  </div>
</section>

<section class="panel panel--front">
  <div class="family-photo" role="img" aria-label="Photo of a multi-generation family sharing a meal at a dining table"></div>
  <svg class="awareness-ribbon" role="img" aria-label="Purple and blue awareness ribbon with two clasped hands at the crossing" viewBox="0 0 220 360">
    <defs>
      <linearGradient id="ribbonTone" x1="0" y1="0" x2="1" y2="1">
        <stop offset="0" stop-color="#b97ab6"/>
        <stop offset="1" stop-color="#2fa7de"/>
      </linearGradient>
    </defs>
    <rect x="0" y="0" width="220" height="360" rx="60" fill="url(#ribbonTone)" opacity=".35"/>
  </svg>
  <div class="brand-dot"></div>
  <div class="brand-name front-brand">HELIXORA</div>
  <h2 class="cover-title">Hereditary Cancer<br>Screening</h2>
  <p class="cover-tagline">The Power of Knowledge</p>
  <p class="cancer-list">Breast | Ovarian | Endometrial &nbsp;| Gastric | Colorectal<br>Pancreatic | Melanoma | Prostate | Lung | Colon</p>
</section>

<div class="panel-label panel-label--back">Back</div>
<div class="panel-label panel-label--front">Front</div>

</body>
</html>
```